PlayTallyCollective - Game Statistics and Achievement Tracking

I need a new modern design for an existing website.

The website is a project to track statistics and achievements for games (currently Vaporn Achievements/Stats and stats for Cargo Haul Odyssey 2 and Frontier Rig Journeys).
I am currently expanding the site with other platforms (like QVR) and more games.
I am also adding a user registration/signin with user profiles to show off their achievements and stats across all platforms and games.

The current website is available at https://plytly.example/
To search for data you can use the username "pixelornin" (without quotes).

The design should be modern and extendable and contain space for a logo.

The logo should match the project. It should combine Gaming with statistics.

Target Market(s)

Video game players

Number of Pages Required

5+ page

Font styles to use
Sans Serif

Requirements
Must have
• Basic Layout, User profile page (not yet available on live site), Search Page for Platforms/Games, Platform profile page, Dark theme

```html
<!DOCTYPE html>
<html lang="en">
<head>
<meta charset="utf-8">
<title>PlayTallyCollective – Game Statistics</title>
<link href="https://fonts.googleapis.com/css2?family=Luckiest+Guy&family=Poppins:wght@400;500;600&family=Crimson+Text:wght@400;600;700&display=swap" rel="stylesheet">
<style>
:root{
  --bg:#05070a;
  --bg-2:#0b1016;
  --green:#5ee83a;
  --green-2:#8ef06a;
  --green-light:#a7f59a;
  --card:#000000;
  --line:#1f2a22;
  --text:#ffffff;
  --muted:#c9d1cc;
  --dark-text:#0a0a0a;
}
*{box-sizing:border-box;margin:0;padding:0}
html,body{width:1200px;height:3471px;overflow:hidden}
body{position:relative;background:var(--bg);color:var(--text);font-family:"Poppins",sans-serif}
.abs{position:absolute}
.hero-bg{left:0;top:0;width:1200px;height:690px;background:radial-gradient(ellipse at 50% 70%,#16202a 0%,#0a0e13 55%,#05070a 100%)}
.green-band{left:0;top:690px;width:1200px;height:865px;background:linear-gradient(90deg,#62de3c 0%,#7ee65a 50%,#a2f39d 100%)}
.dark-lower{left:0;top:1555px;width:1200px;height:843px;background:radial-gradient(ellipse at 50% 30%,#121a22 0%,#070a0e 60%,#040506 100%)}
.games-bg{left:0;top:2280px;width:1200px;height:1118px;background:linear-gradient(180deg,#050608,#070a09)}

/* header */
.brand{left:113px;top:40px;width:130px;display:flex;align-items:center;gap:8px}
.brand-dot{width:16px;height:16px;border-radius:50%;background:var(--green)}
.brand-name{font-family:"Poppins",sans-serif;font-weight:600;font-size:20px;color:var(--text);letter-spacing:.5px}
.nav{left:397px;top:52px;display:flex;gap:22px;font-family:"Crimson Text",serif;font-weight:700;font-size:16px}
.nav a{color:var(--text);text-decoration:none}
.nav a.active{color:var(--green)}
.btn-pill{top:40px;height:44px;border:2px solid var(--green);border-radius:22px;background:linear-gradient(180deg,#48d12a,#2fa91a);display:flex;align-items:center;justify-content:center;gap:6px;font-family:"Crimson Text",serif;font-weight:700;font-size:14px;color:#06250a}
.btn-login{left:802px;width:107px}
.btn-register{left:914px;width:174px}

.welcome{left:0;width:1200px;top:155px;text-align:center;font-family:"Crimson Text",serif;font-weight:600;font-size:28px}
.welcome-rule{left:553px;top:198px;width:94px;height:2px;background:var(--green)}
.welcome-rule::after{content:"";position:absolute;left:37px;top:4px;width:20px;height:4px;background:var(--green);border-radius:2px}
.headline{left:0;width:1200px;top:228px;text-align:center;font-family:"Luckiest Guy",sans-serif;font-size:62px;line-height:68px;letter-spacing:1px}
.headline .accent{color:var(--green)}

/* profile card */
.profile{left:110px;top:466px;width:980px;height:427px;background:var(--card);border:2px solid var(--green);border-radius:12px}
.badge{top:38px;width:90px;text-align:center}
.badge .ring{width:42px;height:42px;margin:0 auto;border:1.5px solid #cfd6d0;border-radius:50%;display:flex;align-items:center;justify-content:center;font-size:14px}
.badge .cap{margin-top:10px;font-family:"Crimson Text",serif;font-size:13px;white-space:nowrap}
.badge.first .ring{color:var(--green);border-color:var(--green)}
.badge.first .cap{color:var(--green)}
.flag{width:42px;height:42px;margin:0 auto;border-radius:50%;overflow:hidden;border:1.5px solid #fff;background:linear-gradient(180deg,#000 0 33%,#dd0000 33% 66%,#ffce00 66%)}
.search-pill{height:53px;border:1px solid #3a4038;border-radius:27px;display:flex;align-items:center;padding-left:24px;font-family:"Crimson Text",serif;font-size:17px;color:#fff}
.search-btn{position:absolute;right:6px;top:8px;width:36px;height:36px;border-radius:50%;background:#1b1e1c;display:flex;align-items:center;justify-content:center}
.profile .search-pill{left:576px;top:46px;width:372px}
.profile-rule{left:33px;top:138px;width:914px;height:1px;background:#3a3f3a}
.avatar{left:33px;top:155px;width:256px;height:254px;border:2px solid #2f9bff;background:linear-gradient(160deg,#5fc0ff,#2a7bd1 60%,#173e6b)}
.facts{left:338px;top:166px;font-family:"Crimson Text",serif;font-size:17px}
.fact{display:flex;height:39.4px}
.fact dt{width:153px;font-weight:700}
.fact dd{font-family:"Poppins",sans-serif;font-size:14px;padding-top:2px}
.links{left:790px;top:180px;width:182px;text-align:center;font-family:"Poppins",sans-serif;font-size:15px}
.links a{display:block;color:#fff;text-decoration:none;height:57px}

/* section titles */
.section-title{left:0;width:1200px;text-align:center;font-family:"Luckiest Guy",sans-serif;font-size:56px;letter-spacing:1px}
.users-title{top:962px;color:var(--dark-text)}
.users-copy{left:200px;top:1040px;width:800px;text-align:center;font-size:14px;line-height:25px;color:#1b2a18}

/* users table */
.users-card{left:111px;top:1122px;width:977px;height:724px;background:var(--card);border:1px solid #2b2f2c;border-radius:8px}
.thead{position:absolute;left:11px;top:15px;width:956px;height:73px;border:1px solid #2a2e2b;border-radius:8px;font-size:14px}
.thead span,.row span{position:absolute;top:50%;transform:translateY(-50%)}
.row{position:absolute;left:26px;width:928px;height:94px;border-bottom:1px solid #1e2320;font-size:14px}
.row .pic{left:15px;width:52px;height:52px;border-radius:50%;background:radial-gradient(circle at 50% 40%,#b99a83,#4a3b33)}
.load-more{left:40px;top:668px;width:912px;height:36px;background:var(--green);color:#0c2a06;font-size:13px;display:flex;align-items:center;justify-content:center}

/* statistics */
.stats-title{top:1955px;color:#fff}
.stat{top:2065px;width:200px;text-align:center}
.stat .num{font-family:"Luckiest Guy",sans-serif;color:var(--green);font-size:38px;line-height:44px;margin-top:6px}
.stat .lbl{font-size:14px;margin-top:4px}

/* games */
.games-title{top:2308px;color:#fff}
.filter{left:174px;top:2393px;width:853px;height:134px;border:1px solid #3a403a;border-radius:10px}
.filter-label{top:28px;font-family:"Crimson Text",serif;font-weight:700;font-size:16px;color:var(--green);letter-spacing:.5px}
.filter .search-pill{top:56px;width:372px}
.filter-btn{left:792px;top:65px;width:36px;height:36px;border-radius:50%;background:#1b1e1c;display:flex;align-items:center;justify-content:center}
.tile{width:215px;height:122px;background:#0d100e;border:1px solid #1d231f;padding:5px}
.tile .cover{height:76px}
.tile .bar{height:28px;margin-top:4px;background:var(--green);display:flex;justify-content:space-around;align-items:center;font-size:13px;color:#0b1a08}
.scroll-cue{left:599px;top:3288px;width:2px;height:50px;background:#cfd6d0}

.footer{left:0;top:3398px;width:1200px;height:73px;background:linear-gradient(90deg,#5fdc3a,#a4f3a0);display:flex;align-items:center;justify-content:center;font-size:15px;color:#0d1c0a}
</style>
</head>
<body>

<div class="abs hero-bg"></div>
<div class="abs green-band"></div>
<div class="abs dark-lower"></div>
<div class="abs games-bg"></div>

<!-- header -->
<div class="abs brand"><span class="brand-dot"></span><span class="brand-name">PLAYTALLY</span></div>
<nav class="abs nav">
  <a class="active">HOME</a><a>ABOUT US ⌄</a><a>VAPORN</a><a>GAMES ⌄</a><a>USERS</a>
</nav>
<div class="abs btn-pill btn-login">
  <svg width="11" height="11" viewBox="0 0 12 12"><path d="M1 6h7M5 3l3 3-3 3" stroke="#06250a" stroke-width="2" fill="none"/><path d="M9 1h2v10H9" stroke="#06250a" stroke-width="1.5" fill="none"/></svg>LOGIN</div>
<div class="abs btn-pill btn-register">
  <svg width="11" height="12" viewBox="0 0 12 12"><circle cx="6" cy="3.5" r="3" fill="#06250a"/><path d="M0 12c0-4 3-5 6-5s6 1 6 5z" fill="#06250a"/></svg>REGISTER NOW</div>

<div class="abs welcome">WELCOME TO</div>
<div class="abs welcome-rule"></div>
<h1 class="abs headline"><span class="accent">THE PLAYTALLY</span><br>COLLECTIVE!</h1>

<!-- profile card -->
<section class="abs profile">
  <div class="abs badge first" style="left:29px"><div class="ring">179</div><div class="cap">Vaporn Level</div></div>
  <div class="abs badge" style="left:126px"><div class="ring">179</div><div class="cap">Account Age</div></div>
  <div class="abs badge" style="left:224px"><div class="ring">179</div><div class="cap">Perfect Game</div></div>
  <div class="abs badge" style="left:321px"><div class="flag"></div><div class="cap">Germany</div></div>
  <div class="abs search-pill">Search Vaporn User
    <span class="search-btn"><svg width="14" height="14" viewBox="0 0 14 14"><circle cx="6" cy="6" r="4.2" stroke="#fff" stroke-width="2" fill="none"/><path d="M9 9l4 4" stroke="#fff" stroke-width="2"/></svg></span></div>
  <div class="abs profile-rule"></div>
  <div class="abs avatar" role="img" aria-label="User avatar illustration"></div>
  <dl class="abs facts">
    <div class="fact"><dt>Played Games:</dt><dd>1166 / 1644 (70%)</dd></div>
    <div class="fact"><dt>Total play time:</dt><dd>1 year 2 months 11 hours 25 minutes</dd></div>
    <div class="fact"><dt>Achievements:</dt><dd>18007 / 63070 (28%)</dd></div>
    <div class="fact"><dt>Member since:</dt><dd>14.01.2009</dd></div>
    <div class="fact"><dt>Last played:</dt><dd>Rail Driver Realm 5</dd></div>
    <div class="fact"><dt>Last Update:</dt><dd>26.12.2024 12:53h</dd></div>
  </dl>
  <div class="abs links"><a>Upgrade</a><a>Timeline</a><a>Vaporn Community</a><a>Vaporn DB</a></div>
</section>

<!-- users -->
<h2 class="abs section-title users-title">OUR USERS</h2>
<p class="abs users-copy">Lorem ipsum dolor sit amet, consectetur adipiscing elit, sed do eiusmod tempor incididunt ut labore et dolore magna aliqua. Ut enim ad minim veniam, quis nostrud exercitation ullamco laboris nisi ut aliquip ex ea com</p>

<section class="abs users-card">
  <div class="thead">
    <span style="left:26px">Name</span><span style="left:284px">Level</span><span style="left:464px">Play Time</span><span style="left:636px">Experience</span><span style="left:841px">Active</span>
  </div>
  <div class="row" style="top:88px"><span class="pic"></span><span style="left:81px">Jhon SMith</span><span style="left:269px">High Level</span><span style="left:449px">5 min Ago</span><span style="left:621px">2 Year</span><span style="left:826px">Online</span></div>
  <div class="row" style="top:182px"><span class="pic"></span><span style="left:81px">Jhon SMith</span><span style="left:269px">High Level</span><span style="left:449px">5 min Ago</span><span style="left:621px">2 Year</span><span style="left:826px">Online</span></div>
  <div class="row" style="top:276px"><span class="pic"></span><span style="left:81px">Jhon SMith</span><span style="left:269px">High Level</span><span style="left:449px">5 min Ago</span><span style="left:621px">2 Year</span><span style="left:826px">Online</span></div>
  <div class="row" style="top:370px"><span class="pic"></span><span style="left:81px">Jhon SMith</span><span style="left:269px">High Level</span><span style="left:449px">5 min Ago</span><span style="left:621px">2 Year</span><span style="left:826px">Online</span></div>
  <div class="row" style="top:464px"><span class="pic"></span><span style="left:81px">Jhon SMith</span><span style="left:269px">High Level</span><span style="left:449px">5 min Ago</span><span style="left:621px">2 Year</span><span style="left:826px">Online</span></div>
  <div class="row" style="top:558px"><span class="pic"></span><span style="left:81px">Jhon SMith</span><span style="left:269px">High Level</span><span style="left:449px">5 min Ago</span><span style="left:621px">2 Year</span><span style="left:826px">Online</span></div>
  <div class="abs load-more">LOAD MORE</div>
</section>

<!-- statistics -->
<h2 class="abs section-title stats-title">OUR STATISTICS</h2>
<svg width="0" height="0" style="position:absolute">
  <defs>
    <symbol id="pad" viewBox="0 0 50 34">
      <path d="M12 3h26c6 0 9 5 10 12l1 9c1 6-5 9-9 5l-5-5H15l-5 5c-4 4-10 1-9-5l1-9C3 8 6 3 12 3z" fill="none" stroke="#fff" stroke-width="2.5"/>
      <path d="M14 11v8M10 15h8" stroke="#fff" stroke-width="2.5"/>
      <circle cx="35" cy="12" r="2" fill="#fff"/><circle cx="39" cy="16" r="2" fill="#fff"/><circle cx="31" cy="16" r="2" fill="#fff"/><circle cx="35" cy="20" r="2" fill="#fff"/>
    </symbol>
  </defs>
</svg>
<div class="abs stat" style="left:68px"><svg width="50" height="34"><use href="#pad"/></svg><div class="num">251966</div><div class="lbl">GAMES</div></div>
<div class="abs stat" style="left:284px"><svg width="50" height="34"><use href="#pad"/></svg><div class="num">251966</div><div class="lbl">GAME ACHIEVEMENTS</div></div>
<div class="abs stat" style="left:500px"><svg width="50" height="34"><use href="#pad"/></svg><div class="num">251966</div><div class="lbl">GAME STATS</div></div>
<div class="abs stat" style="left:717px"><svg width="50" height="34"><use href="#pad"/></svg><div class="num">251966</div><div class="lbl">PLAYTIME RECORDS</div></div>
<div class="abs stat" style="left:933px"><svg width="50" height="34"><use href="#pad"/></svg><div class="num">251966</div><div class="lbl">PUBLIC PROFILES</div></div>

<!-- games -->
<h2 class="abs section-title games-title">OUR GAMES</h2>
<section class="abs filter">
  <div class="abs filter-label" style="left:40px">CHOOSE GAME</div>
  <div class="abs filter-label" style="left:426px">CHOOSE BY CATEGORY</div>
  <div class="abs search-pill" style="left:17px">Search Game
    <span class="search-btn"><svg width="14" height="14" viewBox="0 0 14 14"><circle cx="6" cy="6" r="4.2" stroke="#fff" stroke-width="2" fill="none"/><path d="M9 9l4 4" stroke="#fff" stroke-width="2"/></svg></span></div>
  <div class="abs search-pill" style="left:403px">Achievement Progress
    <span class="search-btn"><svg width="12" height="12" viewBox="0 0 12 12"><path d="M2 2l4 4 4-4M2 6l4 4 4-4" stroke="#fff" stroke-width="1.8" fill="none"/></svg></span></div>
  <div class="abs filter-btn"><svg width="13" height="13" viewBox="0 0 13 13"><path d="M0 0h13L8 6v6L5 10V6z" fill="#fff"/></svg></div>
</section>

<div class="abs tile" style="left:138px;top:2585px"><div class="cover" role="img" aria-label="Game cover art" style="background:linear-gradient(135deg,#2d3f7a,#d9764a,#39456e)"></div><div class="bar"><span>5h</span><span>1 / 1</span><span>100%</span></div></div>
<div class="abs tile" style="left:373px;top:2585px"><div class="cover" role="img" aria-label="Game cover art" style="background:linear-gradient(135deg,#2a2222,#5a2a24,#1b1414)"></div><div class="bar"><span>5h</span><span>1 / 1</span><span>100%</span></div></div>
<div class="abs tile" style="left:608px;top:2585px"><div class="cover" role="img" aria-label="Game cover art" style="background:linear-gradient(135deg,#3a6fd8,#a04bd0,#4a2a8a)"></div><div class="bar"><span>5h</span><span>1 / 1</span><span>100%</span></div></div>
<div class="abs tile" style="left:843px;top:2585px"><div class="cover" role="img" aria-label="Game cover art" style="background:linear-gradient(135deg,#3a4a5c,#1f2630,#5a2020)"></div><div class="bar"><span>5h</span><span>1 / 1</span><span>100%</span></div></div>

<div class="abs tile" style="left:138px;top:2724px"><div class="cover" role="img" aria-label="Game cover art" style="background:linear-gradient(135deg,#2a0e12,#b82a2a,#3a0e12)"></div><div class="bar"><span>5h</span><span>1 / 1</span><span>100%</span></div></div>
<div class="abs tile" style="left:373px;top:2724px"><div class="cover" role="img" aria-label="Game cover art" style="background:linear-gradient(135deg,#5fc06a,#e6d88a,#4aa0d8)"></div><div class="bar"><span>5h</span><span>1 / 1</span><span>100%</span></div></div>
<div class="abs tile" style="left:608px;top:2724px"><div class="cover" role="img" aria-label="Game cover art" style="background:linear-gradient(135deg,#8fe08a,#4ac0a0,#9ae88a)"></div><div class="bar"><span>5h</span><span>1 / 1</span><span>100%</span></div></div>
<div class="abs tile" style="left:843px;top:2724px"><div class="cover" role="img" aria-label="Game cover art" style="background:linear-gradient(135deg,#1a1c20,#2c3038,#15171a)"></div><div class="bar"><span>5h</span><span>1 / 1</span><span>100%</span></div></div>

<div class="abs tile" style="left:138px;top:2864px"><div class="cover" role="img" aria-label="Game cover art" style="background:linear-gradient(135deg,#1e2a5a,#3a5aa0,#c09030)"></div><div class="bar"><span>5h</span><span>1 / 1</span><span>100%</span></div></div>
<div class="abs tile" style="left:373px;top:2864px"><div class="cover" role="img" aria-label="Game cover art" style="background:linear-gradient(135deg,#1a2a1c,#2e3a30,#101812)"></div><div class="bar"><span>5h</span><span>1 / 1</span><span>100%</span></div></div>
<div class="abs tile" style="left:608px;top:2864px"><div class="cover" role="img" aria-label="Game cover art" style="background:linear-gradient(135deg,#1a5a3a,#0e0e0e,#0e0e0e)"></div><div class="bar"><span>5h</span><span>1 / 1</span><span>100%</span></div></div>
<div class="abs tile" style="left:843px;top:2864px"><div class="cover" role="img" aria-label="Game cover art" style="background:linear-gradient(135deg,#c05a2a,#e0a040,#5a3a8a)"></div><div class="bar"><span>5h</span><span>1 / 1</span><span>100%</span></div></div>

<div class="abs tile" style="left:138px;top:3003px"><div class="cover" role="img" aria-label="Game cover art" style="background:linear-gradient(135deg,#5ad0e0,#d06ac0,#8a5ae0)"></div><div class="bar"><span>5h</span><span>1 / 1</span><span>100%</span></div></div>
<div class="abs tile" style="left:373px;top:3003px"><div class="cover" role="img" aria-label="Game cover art" style="background:linear-gradient(135deg,#3a2a2a,#8a5a3a,#2a1e1e)"></div><div class="bar"><span>5h</span><span>1 / 1</span><span>100%</span></div></div>
<div class="abs tile" style="left:608px;top:3003px"><div class="cover" role="img" aria-label="Game cover art" style="background:linear-gradient(135deg,#c8c090,#8aa070,#d8d0b0)"></div><div class="bar"><span>5h</span><span>1 / 1</span><span>100%</span></div></div>
<div class="abs tile" style="left:843px;top:3003px"><div class="cover" role="img" aria-label="Game cover art" style="background:linear-gradient(135deg,#2a2220,#4a3a34,#141010)"></div><div class="bar"><span>5h</span><span>1 / 1</span><span>100%</span></div></div>

<div class="abs tile" style="left:138px;top:3142px"><div class="cover" role="img" aria-label="Game cover art" style="background:linear-gradient(135deg,#8a8a90,#c0bcb4,#5a5a60)"></div><div class="bar"><span>5h</span><span>1 / 1</span><span>100%</span></div></div>
<div class="abs tile" style="left:373px;top:3142px"><div class="cover" role="img" aria-label="Game cover art" style="background:linear-gradient(135deg,#c8d0d8,#8a9aa8,#e0e4e8)"></div><div class="bar"><span>5h</span><span>1 / 1</span><span>100%</span></div></div>
<div class="abs tile" style="left:608px;top:3142px"><div class="cover" role="img" aria-label="Game cover art" style="background:linear-gradient(135deg,#8a1a1a,#d83a2a,#5a1010)"></div><div class="bar"><span>5h</span><span>1 / 1</span><span>100%</span></div></div>
<div class="abs tile" style="left:843px;top:3142px"><div class="cover" role="img" aria-label="Game cover art" style="background:linear-gradient(135deg,#0e0e0e,#3a3a3a,#101010)"></div><div class="bar"><span>5h</span><span>1 / 1</span><span>100%</span></div></div>

<div class="abs scroll-cue"></div>
<svg class="abs" style="left:593px;top:3342px" width="14" height="14" viewBox="0 0 14 14"><path d="M2 2l5 5 5-5M2 7l5 5 5-5" stroke="#cfd6d0" stroke-width="1.6" fill="none"/></svg>

<footer class="abs footer">Copyright@2025- All Rights Reserved</footer>

</body>
</html>
```